Website for Excavator and Earthworks Company

We require a modern, sleek and practical website for our newly created earthworks/excavator business in Perth, Western Australia called Bluegum Ridge Earthworks.

The website should have a modern, cutting edge feel but only needs to be relatively simplistic in it's layout and eventual functionality.

Some pages it should have would be Home, About, Projects and Contact Us.

```html
<!DOCTYPE html>
<html lang="en">
<head>
<meta charset="utf-8">
<title>Bluegum Ridge Earthworks</title>
<link href="https://fonts.googleapis.com/css2?family=Michroma&family=Outfit:wght@300;400;500;600&display=swap" rel="stylesheet">
<style>
:root{
  --lime:#cde000;
  --ink:#111111;
  --dark:#1b2228;
  --white:#ffffff;
  --muted:#3a3a3a;
  --line:#dddddd;
}
*{box-sizing:border-box;margin:0;padding:0}
html,body{width:1200px;height:3599px;overflow:hidden;background:var(--white)}
body{position:relative;font-family:"Outfit",sans-serif;color:var(--ink)}
.abs{position:absolute}
.display{font-family:"Michroma",sans-serif;text-transform:uppercase;letter-spacing:1px}

/* brand */
.brand{display:flex;align-items:center;gap:10px}
.brand-mark{width:34px;height:34px;background:var(--lime)}
.brand-name{font-family:"Outfit",sans-serif;font-weight:600;font-size:17px;line-height:1.1;color:var(--ink);text-transform:uppercase;letter-spacing:.5px}

/* nav */
.site-header{left:0;top:0;width:1200px;height:91px}
.nav a{position:absolute;top:36px;font-family:"Michroma",sans-serif;font-size:11px;color:var(--ink);text-decoration:none;letter-spacing:.5px}
.btn{display:flex;align-items:center;justify-content:center;background:var(--lime);font-family:"Michroma",sans-serif;font-size:11.5px;color:var(--ink);letter-spacing:1px;text-transform:uppercase;clip-path:polygon(0 0,100% 0,94% 100%,0 100%)}
.btn-edge{position:absolute;width:4px;background:var(--lime);transform:skewX(-17deg)}

/* hero */
.hero-photo{left:0;top:91px;width:1200px;height:705px;
  background:linear-gradient(90deg,#070605 0%,#1d130c 30%,rgba(0,0,0,0) 60%),
  linear-gradient(170deg,#6b3a1c 0%,#c96a2a 30%,#7a4a2c 55%,#3a2619 80%,#23180f 100%);
  clip-path:polygon(0 0,100% 0,100% 579px,601px 689px,0 533px)}
.tag{display:flex;align-items:center;gap:8px;height:32px;padding:0 22px;font-size:12px;text-transform:uppercase;border:1px solid;clip-path:polygon(0 0,100% 0,94% 100%,0 100%)}
.tag::before{content:"";width:5px;height:5px;border-radius:50%;background:var(--lime)}
.tag.light{color:var(--white);border-color:rgba(255,255,255,.55)}
.tag.darkline{color:var(--ink);border-color:#cfcfcf}
.hero-title{left:141px;top:240px;font-size:42px;line-height:63px;color:var(--white)}
.hero-copy{left:141px;top:432px;width:440px;font-size:16.5px;line-height:29px;color:var(--white)}

/* about */
.about-frame{left:183px;top:869px;width:342px;height:374px;border:2px solid var(--lime)}
.photo{display:block}
.about-main{left:0;top:886px;width:506px;height:525px;background:linear-gradient(160deg,#f3c27a 0%,#d97a2e 35%,#7a5a44 70%,#6c6c68 100%)}
.about-small{left:334px;top:1242px;width:264px;height:220px;background:var(--white);padding:8px}
.about-small .photo{width:100%;height:100%;background:linear-gradient(180deg,#8e8d88 0%,#b6aa92 40%,#6d5a44 100%)}
.section-h{font-size:33px;line-height:42px;color:var(--ink)}
.about-copy{left:630px;top:1030px;width:430px;font-size:12.5px;line-height:22.6px;color:var(--muted)}
.about-copy p+p{margin-top:7px}

/* services */
.svc{top:1551px;height:327px;color:var(--white);text-align:center}
.svc .photo{position:absolute;inset:0}
.svc .shade{position:absolute;inset:0;background:rgba(10,12,14,.45)}
.svc-title{position:absolute;left:0;right:0;top:153px;font-size:19px}
.svc-icon{position:absolute;left:50%;top:88px;transform:translateX(-50%)}
.arrow-btn{position:absolute;left:50%;transform:translateX(-50%);width:46px;height:40px;background:var(--lime);display:flex;align-items:center;justify-content:center;clip-path:polygon(0 0,100% 0,82% 100%,0 100%)}
.arrow-btn.black{background:var(--ink)}
.svc-feature{left:258px;top:1547px;width:425px;height:335px;background:var(--lime);color:var(--ink);text-align:center}
.svc-feature .svc-title{top:125px;font-size:20px}
.svc-feature p{position:absolute;left:50px;right:50px;top:153px;font-size:12.5px;line-height:22.6px}

/* gallery */
.gallery .photo{position:absolute}

/* contact */
.contact{left:0;top:2724px;width:1200px;height:695px;background:linear-gradient(180deg,#1c242b 0%,#232a2c 55%,#2d2a22 100%)}
.contact-copy{left:141px;top:2948px;width:420px;font-size:12.5px;line-height:23px;color:var(--white)}
.info{left:141px;display:flex;gap:20px;color:var(--white)}
.info-label{font-size:12.5px}
.info-val{font-size:12px;line-height:18px;margin-top:4px;opacity:.9}
.social{top:3244px;width:28px;height:28px;border-radius:50%;border:1.5px solid var(--white)}
.social.on{background:var(--lime);border-color:var(--lime)}
.inquiry{left:629px;top:2819px;width:429px;height:506px;background:var(--lime)}
.inquiry h3{position:absolute;left:0;right:0;top:38px;text-align:center;font-size:26px;letter-spacing:2px}
.field{position:absolute;left:30px;width:369px;border:1px solid rgba(255,255,255,.9)}
.field label{position:absolute;left:12px;top:-9px;background:var(--lime);padding:0 5px;font-size:11.5px}
.field span{position:absolute;left:16px;top:15px;font-size:11.5px;color:#3c4200}
.field svg{position:absolute;right:20px;top:16px}
.submit{position:absolute;left:30px;top:415px;width:369px;height:42px;background:var(--ink);color:var(--white);display:flex;align-items:center;justify-content:center;font-family:"Michroma",sans-serif;font-size:11.5px;letter-spacing:2px}

/* footer */
.footer-nav a{position:absolute;top:3468px;font-family:"Michroma",sans-serif;font-size:11px;color:var(--ink);text-decoration:none}
.footer-rule{left:141px;top:3537px;width:922px;height:1px;background:var(--line)}
.copyright{left:0;width:1200px;top:3558px;text-align:center;font-size:12px;color:var(--muted)}
</style>
</head>
<body>

<!-- header -->
<header class="abs site-header">
  <div class="abs brand" style="left:142px;top:28px">
    <span class="brand-mark"></span>
    <span class="brand-name">Bluegum Ridge<br>Earthworks</span>
  </div>
  <nav class="nav">
    <a style="left:476px">HOME</a>
    <a style="left:554px">ABOUT US</a>
    <a style="left:664px">PROJECTS</a>
    <a style="left:778px">CONTACT US</a>
  </nav>
  <a class="abs btn" style="left:911px;top:25px;width:141px;height:39px">Get Quote</a>
  <span class="btn-edge" style="left:1051px;top:25px;height:39px"></span>
</header>

<!-- hero -->
<svg class="abs" style="left:0;top:600px" width="1200" height="200" viewBox="0 600 1200 200">
  <polygon points="0,624 601,780 1200,670 1200,686 601,797 0,640" fill="#cde000"/>
</svg>
<div class="abs hero-photo" role="img" aria-label="Excavator digging into earth at sunset"></div>
<div class="abs tag light" style="left:141px;top:186px;width:310px">Perth's Trusted Earthworks Experts</div>
<h1 class="abs display hero-title">Moving<br>Earth, Building<br>Futures</h1>
<p class="abs hero-copy">Professional Excavation, Site Preparation, And Earthmoving Services Across Perth And Western Australia. Quality Work, Delivered On Time.</p>
<a class="abs btn" style="left:141px;top:538px;width:214px;height:39px">Start Your Project</a>
<span class="btn-edge" style="left:356px;top:538px;height:39px"></span>

<!-- about -->
<section>
  <div class="abs about-frame"></div>
  <div class="abs photo about-main" role="img" aria-label="Orange excavator loading rocks at sunrise"></div>
  <div class="abs about-small"><div class="photo" role="img" aria-label="Loader bucket lifting soil"></div></div>
  <div class="abs tag darkline" style="left:630px;top:890px;width:136px">Who We Are</div>
  <h2 class="abs display section-h" style="left:630px;top:933px">About<br>Bluegum Ridge</h2>
  <div class="abs about-copy">
    <p>Bluegum Ridge Earthworks Is A Locally Owned And Operated Earthmoving Company Serving Perth And Surrounding Areas. With Over 15 Years Of Experience, We've Built Our Reputation On Reliability, Precision, And Exceptional Customer Service.</p>
    <p>Lorem Ipsum Is Simply Dummy Text Of The Printing And Typesetting Industry. Lorem Ipsum Has Been The Industry's Standard Dummy Text Ever Since The 1500s, When An Unknown Printer Took A Galley Of Type And Scrambled It To Make A Type Specimen Book. It Has Survived Not Only Five Centuries, But Also The Leap Into Electronic Typesetting, Remaining Essentially Unchanged. It Was Popularised In The 1960s With The Release Of Letraset Sheets Containing Lorem Ipsum Passages, And More Recently With Desktop.</p>
  </div>
  <a class="abs btn" style="left:630px;top:1334px;width:142px;height:39px">Read More</a>
  <span class="btn-edge" style="left:773px;top:1334px;height:39px"></span>
</section>

<!-- services -->
<section>
  <div class="abs svc" style="left:0;width:256px">
    <div class="photo" style="background:linear-gradient(180deg,#4a5057,#5c5238 60%,#3d3326)" role="img" aria-label="Yellow excavator on a dig site"></div>
    <div class="shade"></div>
    <svg class="svc-icon" width="44" height="40" viewBox="0 0 44 40"><rect x="4" y="22" width="30" height="10" fill="#cde000"/><rect x="14" y="8" width="12" height="14" fill="#cde000"/><rect x="6" y="33" width="26" height="5" rx="2" fill="#cde000"/></svg>
    <div class="svc-title display">Excavation</div>
    <div class="arrow-btn" style="top:201px"><svg width="14" height="14" viewBox="0 0 14 14"><path d="M2 12 12 2M5 2h7v7" stroke="#111" stroke-width="1.6" fill="none"/></svg></div>
  </div>
  <div class="abs svc-feature">
    <svg class="svc-icon" style="top:58px" width="40" height="36" viewBox="0 0 40 36"><rect x="2" y="6" width="22" height="28" fill="#111"/><rect x="24" y="14" width="14" height="20" fill="#111"/><g fill="#cde000"><rect x="6" y="10" width="4" height="4"/><rect x="14" y="10" width="4" height="4"/><rect x="6" y="18" width="4" height="4"/><rect x="14" y="18" width="4" height="4"/><rect x="28" y="18" width="4" height="4"/><rect x="28" y="26" width="4" height="4"/></g></svg>
    <svg class="abs" style="left:0;top:0" width="425" height="335"><path d="M310 12H412V72" stroke="#111" stroke-width="1.2" fill="none"/><path d="M15 255V320H112" stroke="#111" stroke-width="1.2" fill="none"/></svg>
    <div class="svc-title display">Site Preparation</div>
    <p>Lorem Ipsum Is Simply Dummy Text Of The Printing And Typesetting Industry. Lorem Ipsum Has Setting Been The Industry's Standard Dummy Text Ever Since.</p>
    <div class="arrow-btn black" style="top:243px"><svg width="14" height="14" viewBox="0 0 14 14"><path d="M2 12 12 2M5 2h7v7" stroke="#fff" stroke-width="1.6" fill="none"/></svg></div>
  </div>
  <div class="abs svc" style="left:686px;width:256px">
    <div class="photo" style="background:linear-gradient(180deg,#2f3a2c,#5a5440 55%,#6d5a3f)" role="img" aria-label="Bulldozer clearing land in a forest"></div>
    <div class="shade"></div>
    <svg class="svc-icon" width="48" height="36" viewBox="0 0 48 36"><rect x="6" y="6" width="18" height="14" fill="#cde000"/><rect x="2" y="22" width="34" height="10" rx="5" fill="#cde000"/><rect x="38" y="16" width="6" height="18" fill="#cde000"/></svg>
    <div class="svc-title display">Land Clearing</div>
    <div class="arrow-btn" style="top:201px"><svg width="14" height="14" viewBox="0 0 14 14"><path d="M2 12 12 2M5 2h7v7" stroke="#111" stroke-width="1.6" fill="none"/></svg></div>
  </div>
  <div class="abs svc" style="left:944px;width:256px">
    <div class="photo" style="background:linear-gradient(180deg,#5b6166,#7b5a3c 55%,#8a5c36)" role="img" aria-label="Excavator digging a trench"></div>
    <div class="shade"></div>
    <svg class="svc-icon" width="40" height="36" viewBox="0 0 40 36"><rect x="4" y="4" width="32" height="28" fill="#cde000"/><path d="M10 12v14h20V12" stroke="#111" stroke-width="2" fill="none"/></svg>
    <div class="svc-title display">Trenching</div>
    <div class="arrow-btn" style="top:201px"><svg width="14" height="14" viewBox="0 0 14 14"><path d="M2 12 12 2M5 2h7v7" stroke="#111" stroke-width="1.6" fill="none"/></svg></div>
  </div>
</section>

<!-- projects -->
<section class="gallery">
  <div class="abs tag darkline" style="left:527px;top:1975px;width:152px">Work Gallery</div>
  <h2 class="abs display section-h" style="left:0;width:1200px;top:2016px;text-align:center">Out Projects</h2>
  <div class="photo" style="left:141px;top:2080px;width:240px;height:193px;background:linear-gradient(180deg,#5a7aa0,#d79a52 55%,#5a4a34)" role="img" aria-label="Excavator at dusk"></div>
  <div class="photo" style="left:141px;top:2277px;width:240px;height:280px;background:linear-gradient(160deg,#4d4d4d,#2e2e2e 50%,#8a7a3a)" role="img" aria-label="Loader filling a dump truck at a quarry"></div>
  <div class="photo" style="left:386px;top:2080px;width:403px;height:299px;background:linear-gradient(180deg,#5c86b8,#e0b070 55%,#6d5236)" role="img" aria-label="Excavator and dump truck on a site at sunset"></div>
  <div class="photo" style="left:386px;top:2382px;width:116px;height:175px;background:linear-gradient(180deg,#7d7b76,#9f8564 50%,#5c4630)" role="img" aria-label="Loader bucket with soil"></div>
  <div class="photo" style="left:504px;top:2382px;width:285px;height:175px;background:linear-gradient(180deg,#3f7fd0,#8ab4e4 45%,#a07a4a)" role="img" aria-label="Yellow excavator loading a truck"></div>
  <div class="photo" style="left:792px;top:2080px;width:266px;height:193px;background:linear-gradient(180deg,#40567a,#c78a4c 55%,#7a5236)" role="img" aria-label="Backhoe loader on red earth"></div>
  <div class="photo" style="left:792px;top:2277px;width:266px;height:280px;background:linear-gradient(180deg,#2f73c2,#a8c8ea 55%,#b39060)" role="img" aria-label="Yellow excavator against a blue sky"></div>
  <a class="abs btn" style="left:482px;top:2593px;width:230px;height:39px">Discuss Your Project</a>
  <span class="btn-edge" style="left:713px;top:2593px;height:39px"></span>
</section>

<!-- contact -->
<section>
  <div class="abs contact" role="img" aria-label="Excavator on a dusk worksite, darkened"></div>
  <div class="abs tag light" style="left:141px;top:2850px;width:120px">Contact</div>
  <h2 class="abs display section-h" style="left:141px;top:2891px;color:var(--white)">Contact Details</h2>
  <p class="abs contact-copy">Lorem Ipsum Odor Amet, Consectetuer Adipiscing Elit. Cubilia Montes Libero Sagittis Torquent Purus Platea.Facilisi Donec .</p>
  <div class="abs info" style="top:3022px">
    <svg width="44" height="44" viewBox="0 0 44 44"><rect x="8" y="6" width="18" height="32" fill="none" stroke="#cde000" stroke-width="2"/><rect x="26" y="16" width="10" height="22" fill="none" stroke="#cde000" stroke-width="2"/><path d="M13 12h3M19 12h3M13 18h3M19 18h3M13 24h3M19 24h3" stroke="#cde000" stroke-width="2"/></svg>
    <div><div class="info-label">Location</div><div class="info-val">123 Lorem Ipsum Odor Ametconsectetuer<br>Adipiscing Elit. Cubilia Montes.</div></div>
  </div>
  <div class="abs info" style="top:3103px">
    <svg width="44" height="44" viewBox="0 0 44 44"><rect x="6" y="14" width="32" height="22" fill="none" stroke="#cde000" stroke-width="2"/><path d="M6 14l16 12 16-12" fill="none" stroke="#cde000" stroke-width="2"/></svg>
    <div><div class="info-label">Email Address</div><div class="info-val">info@bluegumridge.com.au</div></div>
  </div>
  <div class="abs info" style="top:3175px">
    <svg width="44" height="44" viewBox="0 0 44 44"><path d="M12 6l6 8-4 4c2 5 6 9 11 11l4-4 8 6-4 6C20 36 8 24 6 12z" fill="none" stroke="#cde000" stroke-width="2"/></svg>
    <div><div class="info-label">Phone Number</div><div class="info-val" style="font-size:15px">(123) 456 7890</div></div>
  </div>
  <span class="abs social" style="left:143px" aria-label="Social profile"></span>
  <span class="abs social on" style="left:182px" aria-label="Social profile"></span>
  <span class="abs social" style="left:221px" aria-label="Social profile"></span>
  <span class="abs social" style="left:260px" aria-label="Social profile"></span>

  <form class="abs inquiry">
    <h3 class="display">Quick Inquiry</h3>
    <div class="field" style="top:97px;height:47px"><label>Full Name</label><span>Enter Your Name</span>
      <svg width="12" height="12" viewBox="0 0 12 12"><circle cx="6" cy="3.5" r="2.5" fill="#111"/><path d="M1 12c0-4 10-4 10 0z" fill="#111"/></svg></div>
    <div class="field" style="top:161px;height:47px"><label>Phone No</label><span>123 456 7890</span>
      <svg width="12" height="12" viewBox="0 0 12 12"><path d="M2 1l2 3-1 1.5c1 2 2 3 3.5 3.5L8 8l3 2-1 2C5 12 0 7 0 2z" fill="#111"/></svg></div>
    <div class="field" style="top:228px;height:47px"><label>Email Address</label><span>you@mailbox.com</span>
      <svg width="14" height="11" viewBox="0 0 14 11"><rect width="14" height="11" rx="1" fill="#111"/><path d="M1 1l6 5 6-5" stroke="#cde000" fill="none"/></svg></div>
    <div class="field" style="top:295px;height:98px"><label>Message</label><span>Type Your Message Here!</span>
      <svg width="12" height="12" viewBox="0 0 12 12"><circle cx="6" cy="6" r="6" fill="#111"/></svg></div>
    <div class="submit">SUBMIT NOW</div>
  </form>
</section>

<!-- footer -->
<footer>
  <div class="abs brand" style="left:142px;top:3457px">
    <span class="brand-mark"></span>
    <span class="brand-name">Bluegum Ridge<br>Earthworks</span>
  </div>
  <nav class="footer-nav">
    <a style="left:616px">HOME</a>
    <a style="left:717px">ABOUT US</a>
    <a style="left:838px">PROJECTS</a>
    <a style="left:964px">CONTACT US</a>
  </nav>
  <div class="abs footer-rule"></div>
  <p class="abs copyright">© 2026 Bluegum Ridge. All Rights Reserved.</p>
</footer>

</body>
</html>
```